Corvin Ridge Software PowerPoint template

We are a software company selling endpoint visibility, access and security technology to enterprise-level IT departments.
Our technology helps organizations gain comprehensive visibility into and control over devices accessing their corporate network so they can quickly identify and address suspicious activity on the network that could lead to potential threats like data breaches.
This technology can cost organizations upwards of $1M - depending on the size of the organization. Our primary clients are Vestral 2,000 companies.
We want a professional, polished PowerPoint template that we can use for all company presentations. Please include:
Title page
Section page
General info page
Thank you page
Logo options and color specs are attached.
Please include our tagline on at least the title page: Discover the edge. Optimize the whole.
Reason: Seeking more options. Looking for a clean design that uses lots of white space.
Software

```html
<!DOCTYPE html>
<html lang="en">
<head>
<meta charset="utf-8">
<title>Corvin Ridge Software – Title Slide</title>
<link rel="stylesheet" href="https://fonts.googleapis.com/css2?family=Exo+2:wght@300;500;600;700&display=swap">
<style>
  :root {
    --copper: #b9684a;
    --copper-soft: #c77a5a;
    --brick: #9b2a2f;
    --mist: #e8e8ea;
    --slate: #6d6e70;
    --rule: #8c8c8e;
    --paper: #ffffff;
  }
  * { margin: 0; padding: 0; box-sizing: border-box; }
  html, body {
    width: 1200px; height: 849px; overflow: hidden;
    background: var(--paper);
    font-family: "Exo 2", sans-serif;
  }
  .slide {
    position: relative; width: 1200px; height: 849px;
    overflow: hidden; background: var(--paper);
  }
  .corner-accent {
    position: absolute; right: 0; top: 0;
    width: 390px; height: 370px;
    background: radial-gradient(ellipse at 75% 25%, rgba(185,104,74,0.55) 0%, rgba(199,122,90,0.30) 35%, rgba(232,232,234,0.55) 60%, rgba(255,255,255,0) 80%);
  }
  .brand {
    position: absolute; left: 107px; top: 100px;
    display: flex; align-items: center; gap: 34px;
  }
  .brand-mark {
    width: 74px; height: 74px; border-radius: 50%;
    background: var(--brick);
  }
  .brand-name {
    color: var(--brick); font-weight: 500;
    line-height: 1.05; text-transform: uppercase;
  }
  .brand-name .line-one { display: block; font-size: 44px; letter-spacing: 6px; }
  .brand-name .line-two { display: block; font-size: 27px; letter-spacing: 17px; margin-top: 4px; }
  .hero-circle {
    position: absolute; left: 86px; top: 238px;
    width: 542px; height: 542px; border-radius: 50%;
    background: var(--copper);
  }
  .tagline {
    position: absolute; left: 192px; top: 378px;
    color: var(--paper); font-weight: 300;
    font-size: 58px; line-height: 66px;
    text-transform: uppercase; letter-spacing: 0.5px;
  }
  .presentee {
    position: absolute; right: 63px; top: 436px; text-align: right;
    color: var(--slate); text-transform: uppercase;
  }
  .presentee .name { font-size: 19px; font-weight: 600; }
  .presentee .date { font-size: 17px; font-weight: 500; margin-top: 10px; }
  .divider {
    position: absolute; left: 652px; right: 0; top: 507px;
    height: 1.5px; background: var(--rule);
  }
  .website {
    position: absolute; right: 75px; top: 741px;
    color: var(--brick); font-size: 17px; font-weight: 500;
    text-transform: uppercase;
  }
  .website strong { font-weight: 700; }
</style>
</head>
<body>
  <main class="slide">
    <div class="corner-accent" role="img" aria-label="Decorative cluster of copper and grey dots"></div>

    <div class="brand">
      <span class="brand-mark"></span>
      <p class="brand-name">
        <span class="line-one">Corvin Ridge</span>
        <span class="line-two">Software</span>
      </p>
    </div>

    <div class="hero-circle"></div>
    <h1 class="tagline">Discover<br>the edge,<br>optimize<br>the whole</h1>

    <div class="presentee">
      <p class="name">Name of the presentee</p>
      <p class="date">Date : MM DD YY</p>
    </div>
    <div class="divider"></div>

    <p class="website">www.<strong>corvinridge</strong>software.com</p>
  </main>
</body>
</html>
```